Financial Services Consultant needs a business card

We need a business card for a new consulting company based in Melbourne called
"Quelbrook Insights". Tagline is Measure, Monitor, Save
We would like to see business card designs that are in line with the minimal style of the website www.quelbrook-insights.example
The font I have used on the website is Proxima Nova and would like the same or similar font used on the business card with a minimal design in line with the website Two sided with "QUELBROOK INSIGHTS" MEASURE, MONITOR, SAVE on one side and name, title and contact details on the otther
Updates

Hi All, thanks for your submissions, much appreciated.

I have recently added some colour to my webiste, it is hex #3a7b74 for those that wish to use it
Thanks

Hi all

thanks very much for your design submissions I am very impressed and they are much appreciated.

Interms of general feedback please find below;

Colour: I am trying to stick to a minimal design and colour scheme for my website which is still under construction, up to 3 colours( www.quelbrook-insights.example) it is currently black and white with a small amount of blue/green but I am open to suggestion/interpretations for a consulting company.

Card: I dont mind if it has rounded edges or straight, I was thinking about using a letterpress card if possible

Detail: the detail on the card will include; Name, Title, Mobile, Personal Email, Business Email,Web,Business Address

Once again thanks for submissions

Industry/Entity Type

Business

```html
<!DOCTYPE html>
<html lang="en">
<head>
<meta charset="utf-8">
<title>Quelbrook Insights – Business Card</title>
<link rel="stylesheet" href="https://fonts.googleapis.com/css2?family=Montserrat:wght@700&family=Open+Sans:wght@400;600;700&display=swap">
<style>
  :root {
    --backdrop: #e4e4e8;
    --card: #ffffff;
    --ink: #111111;
    --text: #3a3a3a;
    --muted: #555555;
    --teal: #3a7b74;
    --band: #141212;
    --shadow: rgba(40, 40, 60, 0.18);
  }
  * { box-sizing: border-box; margin: 0; padding: 0; }
  html, body {
    width: 1200px;
    height: 987px;
    overflow: hidden;
    background: var(--backdrop);
  }
  .stage {
    width: 1200px;
    height: 987px;
    display: flex;
    align-items: center;
    justify-content: center;
    gap: 40px;
  }
  .card {
    position: relative;
    width: 540px;
    height: 309px;
    background: var(--card);
    border-radius: 28px;
    overflow: hidden;
    box-shadow: 0 10px 30px var(--shadow);
  }
  .wordmark {
    font-family: "Montserrat", sans-serif;
    font-weight: 700;
    color: var(--ink);
    letter-spacing: 0.06em;
    white-space: nowrap;
  }

  /* Contact side */
  .card--contact .wordmark {
    position: absolute;
    left: 34px;
    top: 34px;
    font-size: 31px;
  }
  .contact-list {
    position: absolute;
    left: 40px;
    top: 104px;
    font-family: "Open Sans", sans-serif;
    color: var(--text);
    list-style: none;
  }
  .contact-name {
    font-size: 17px;
    font-weight: 700;
    color: #4a4a4a;
    margin-bottom: 8px;
  }
  .contact-title { font-weight: 400; color: var(--teal); }
  .contact-item {
    display: flex;
    align-items: center;
    gap: 8px;
    font-size: 13px;
    margin-bottom: 6px;
  }
  .contact-item svg { width: 12px; height: 12px; flex: none; }
  .address-band {
    position: absolute;
    left: 0;
    right: 0;
    bottom: 0;
    height: 52px;
    background: var(--band);
    border-top: 3px solid var(--teal);
    display: flex;
    align-items: center;
    padding-left: 36px;
    font-family: "Open Sans", sans-serif;
    font-size: 14px;
    color: #ffffff;
  }

  /* Brand side */
  .card--brand {
    display: flex;
    flex-direction: column;
    align-items: center;
    justify-content: center;
  }
  .card--brand .wordmark { font-size: 30px; }
  .tagline {
    font-family: "Open Sans", sans-serif;
    font-size: 15px;
    color: var(--muted);
    margin-top: 10px;
  }
  .site-url {
    font-family: "Open Sans", sans-serif;
    font-size: 13px;
    color: var(--text);
    letter-spacing: 0.28em;
    margin-top: 14px;
  }
  .site-url strong { font-weight: 700; }
</style>
</head>
<body>
<main class="stage">
  <section class="card card--contact" aria-label="Contact side">
    <h1 class="wordmark">QUELBROOK INSIGHTS</h1>
    <ul class="contact-list">
      <li class="contact-name">Your Name, <span class="contact-title">Title</span></li>
      <li class="contact-item">
        <svg viewBox="0 0 12 12" aria-hidden="true"><circle cx="6" cy="6" r="5.3" fill="none" stroke="#444" stroke-width="1"/><path d="M4 3.2c.4-.3.8-.2 1 .2l.4.8c.1.3 0 .5-.2.7l-.3.3c.3.7.9 1.3 1.6 1.6l.3-.3c.2-.2.5-.3.7-.2l.8.4c.4.2.5.6.2 1l-.4.4c-1.8.3-4.6-2.5-4.3-4.3z" fill="#444"/></svg>
        123-456-0789
      </li>
      <li class="contact-item">
        <svg viewBox="0 0 12 12" aria-hidden="true"><circle cx="6" cy="6" r="5.3" fill="#777"/><path d="M.7 6h10.6M6 .7v10.6M2 3.3h8M2 8.7h8" stroke="#fff" stroke-width=".6"/><ellipse cx="6" cy="6" rx="2.4" ry="5.3" fill="none" stroke="#fff" stroke-width=".6"/></svg>
        www.quelbrook-insights.example
      </li>
    </ul>
    <footer class="address-band">Street Name, City Name, State Zip Code</footer>
  </section>

  <section class="card card--brand" aria-label="Brand side">
    <h2 class="wordmark">QUELBROOK INSIGHTS</h2>
    <p class="tagline">Measure, Monitor, Save</p>
    <p class="site-url">www.<strong>quelbrook-insights</strong>.example</p>
  </section>
</main>
</body>
</html>
```